Speisekarten-Design für gehobenes italienisches Restaurant
Zielgruppe
Wir sind ein gehobenes italienisches Restaurant und suchen ein neues Design für unsere Speisekarte. Wir haben ein eher älteres Publikum.
Aufgabenstellung
Wir möchten eine elegantes modernes Design. Einzelseiten im A4 Format.

```html
<!DOCTYPE html>
<html lang="de">
<head>
<meta charset="utf-8">
<title>Speisekarte – Suppen &amp; Antipasti</title>
<link rel="stylesheet" href="https://fonts.googleapis.com/css2?family=Great+Vibes&family=Questrial&display=swap">
<style>
  :root {
    --page: #ffffff;
    --ink: #1b1b1b;
    --ink-soft: #3a3a3a;
    --rule: #2a2a2a;
    --italy-green: #1f9a3a;
    --italy-red: #e31a1a;
    --photo-soup: #c9532d;
    --photo-caprese: #d8d3cf;
  }
  * { margin: 0; padding: 0; box-sizing: border-box; }
  html, body { width: 800px; height: 1200px; overflow: hidden; background: var(--page); }
  body { font-family: "Questrial", "Century Gothic", sans-serif; color: var(--ink); }
  .menu-page { position: relative; width: 800px; height: 1200px; }

  .section-heading { position: absolute; display: flex; align-items: flex-end; font-weight: normal; }
  .section-heading .initial { font-family: "Great Vibes", cursive; font-size: 110px; line-height: .8; }
  .section-heading .rest { font-size: 40px; letter-spacing: 1px; margin-left: -6px; margin-bottom: 6px; }
  .rule { position: absolute; height: 1px; background: var(--rule); }

  .dish-photo { position: absolute; border-radius: 50%; }
  .dish-photo.soup { background: radial-gradient(circle at 50% 45%, #e06a3a, var(--photo-soup) 60%, #9a4325); }
  .dish-photo.caprese { background: radial-gradient(ellipse at 50% 50%, #d9574c 0 35%, #ece8e3 60%, var(--photo-caprese)); }

  .dish-list { position: absolute; list-style: none; }
  .dish { position: relative; margin-bottom: 20px; padding-right: 64px; }
  .dish--price-below { padding-right: 0; padding-bottom: 0; }
  .dish--price-below .dish-price { top: 26px; }
  .dish-name { font-size: 20px; line-height: 1.2; white-space: nowrap; }
  .dish-name sup { font-size: 9px; margin-left: 2px; }
  .dish-desc { font-size: 13px; line-height: 1.3; color: var(--ink-soft); }
  .dish-price { position: absolute; right: 0; top: 2px; font-size: 14px; font-weight: bold; }

  .brand-name { position: absolute; left: 590px; top: 1010px; font-size: 22px; color: var(--ink-soft); }

  .tricolore { position: absolute; left: 130px; top: 1100px; width: 540px; height: 14px; display: flex; }
  .tricolore .green { flex: 1; background: var(--italy-green); }
  .tricolore .white { flex: 1; background: var(--page); border-top: 1px solid var(--rule); border-bottom: 1px solid var(--rule); }
  .tricolore .red { flex: 1; background: var(--italy-red); }
</style>
</head>
<body>
<main class="menu-page">
  <div class="rule" style="left:250px; top:110px; width:320px;"></div>
  <div class="dish-photo soup" role="img" aria-label="Foto: Tomatensuppe in einer Terrakotta-Schale" style="left:585px; top:40px; width:90px; height:64px;"></div>
  <h2 class="section-heading" style="left:320px; top:110px;"><span class="initial">S</span><span class="rest">uppen</span></h2>
  <div class="rule" style="left:220px; top:212px; width:380px;"></div>

  <ul class="dish-list" style="left:240px; top:232px; width:360px;">
    <li class="dish"><div class="dish-name">Tomatensuppe<sup>G</sup></div><div class="dish-desc">Mit Sahnehäubchen aufwartend</div><span class="dish-price">6.60</span></li>
    <li class="dish"><div class="dish-name">Minestrone</div><div class="dish-desc">Mit frischem Gemüse</div><span class="dish-price">6.90</span></li>
    <li class="dish"><div class="dish-name">Tortellini in Brodo<sup>L</sup></div><div class="dish-desc">Hackfleisch gefüllte Tortellini<br>in kräftiger Brühe</div><span class="dish-price">6.90</span></li>
    <li class="dish"><div class="dish-name">Italienische Zwiebelsuppe<sup>G</sup></div><div class="dish-desc">Die feine hausgemachte Suppe erreicht Sie<br>frisch aus dem Ofen mit einer knusprigen<br>Pizzateighaube</div><span class="dish-price">9.50</span></li>
  </ul>

  <div class="rule" style="left:230px; top:560px; width:370px;"></div>
  <h2 class="section-heading" style="left:300px; top:565px;"><span class="initial">A</span><span class="rest">ntipasti</span></h2>
  <div class="dish-photo caprese" role="img" aria-label="Foto: Caprese-Teller mit Tomaten, Mozzarella und Basilikum" style="left:120px; top:590px; width:120px; height:70px;"></div>
  <div class="rule" style="left:260px; top:672px; width:320px;"></div>

  <ul class="dish-list" style="left:60px; top:700px; width:360px;">
    <li class="dish dish--price-below"><div class="dish-name">Gebackener Sachfskäse mit Salat<sup>G</sup></div><div class="dish-desc">Panierter und frittierter Schafskäse<br>an Salatbouquet</div><span class="dish-price">13.90</span></li>
    <li class="dish"><div class="dish-name">Carpaccio di Manzo<sup>G,L</sup></div><div class="dish-desc">Hauchfein geschnittene Rinderfilet-Scheiben<br>auf Rucolabett. Mit frischen Champignons,<br>Parmesankäse &amp; Sellerie</div><span class="dish-price">15.90</span></li>
    <li class="dish"><div class="dish-name">Garnelen-Pfännchen<sup>B</sup></div><div class="dish-desc">Leckere gebratene Garnelen in mit Knoblauch<br>und Kräutern abgeschmeckter Soße</div><span class="dish-price">16.90</span></li>
    <li class="dish"><div class="dish-name">Vitello Tonnato<sup>6,D,G</sup></div><div class="dish-desc">Fein geschnittener Kalbsbraten bedeckt mit<br>Thunfischcreme, angemacht mit Oliven,<br>Kapern &amp; Sardellen</div><span class="dish-price">14.50</span></li>
  </ul>

  <ul class="dish-list" style="left:440px; top:700px; width:320px;">
    <li class="dish"><div class="dish-name">Insalata di Mare<sup>B,D,R</sup></div><div class="dish-desc">Hausgemachter Meeresfrüchte-Salat<br>erwartet Sie hier.<br>Dazu reichen wir Ihnen Brot</div><span class="dish-price">15.90</span></li>
    <li class="dish"><div class="dish-name">Anitpasto Misto<sup>6,B,D,G,R</sup></div><div class="dish-desc">Genießen Sie eine von unserem Küchen-<br>chef zusammengestellte leckere<br>Kombination kalt-warmer Vorspeisen-<br>Spezialitäten aus mediterranen Gefilden</div><span class="dish-price">15.90</span></li>
    <li class="dish"><div class="dish-name">Caprese<sup>G</sup></div><div class="dish-desc">Italienische Vorspeisen-Spezialität u.a. aus<br>Tomatenscheiben, Mozzarella-Käse<br>und Basilikum</div><span class="dish-price">9.90</span></li>
  </ul>

  <p class="brand-name">Casa Serena</p>

  <div class="tricolore" aria-hidden="true"><span class="green"></span><span class="white"></span><span class="red"></span></div>
</main>
</body>
</html>
```